The most modern business card ever !!!

Our company call “Vendalo”. Vendalo is a technology company specialized in cruises solutions. Out main product is a platform to reserve cruises. This is a revolutionary platform that make easier to travel agencies and final users to reserve cruises across dozen companies like tibba, wernu, hpv, dgb, etc..We are a “start up”, with a young team of developers and we want to transmit it.. For it, we want something different, a modern business card that represent cruises and technology.. When someone receive this card, this person should say: wowww this is different… this is modern… this is a cruise related company..
- diferent, modern
- traditions business card

```html
<!DOCTYPE html>
<html lang="en">
<head>
<meta charset="UTF-8">
<title>Vendalo — Business Card</title>
<link href="https://fonts.googleapis.com/css2?family=Exo+2:wght@600;700&family=Open+Sans:wght@400&display=swap" rel="stylesheet">
<style>
  :root {
    --backdrop: #dcdcdc;
    --panel-dark: #000000;
    --panel-light: #f3f3f3;
    --accent: #29a9e1;
    --text-light: #ffffff;
    --text-dark: #0b0b0b;
  }
  * { margin: 0; padding: 0; box-sizing: border-box; }
  html, body {
    width: 1200px;
    height: 900px;
    overflow: hidden;
    background: var(--backdrop);
  }
  .canvas {
    position: relative;
    width: 1200px;
    height: 900px;
  }
  .business-card {
    position: absolute;
    left: 210px;
    top: 210px;
    width: 780px;
    height: 481px;
    display: flex;
    box-shadow: 0 10px 30px rgba(0,0,0,0.18);
  }
  .card-info {
    position: relative;
    width: 402px;
    height: 100%;
    background: var(--panel-dark);
    color: var(--text-light);
    font-family: "Open Sans", sans-serif;
    text-align: right;
    padding-right: 38px;
  }
  .person-name {
    position: absolute;
    right: 38px;
    top: 60px;
    font-family: "Exo 2", sans-serif;
    font-weight: 700;
    font-size: 25px;
    letter-spacing: 0.5px;
    color: var(--accent);
    text-transform: uppercase;
    line-height: 1;
  }
  .person-role {
    position: absolute;
    right: 38px;
    top: 89px;
    font-size: 21px;
    line-height: 1;
  }
  .name-chevron {
    position: absolute;
    right: -2px;
    top: 60px;
    width: 24px;
    height: 46px;
  }
  .contact-list {
    position: absolute;
    right: 14px;
    top: 250px;
    list-style: none;
    font-size: 21px;
    line-height: 28.5px;
  }
  .contact-list li {
    display: flex;
    justify-content: flex-end;
    align-items: center;
    gap: 3px;
  }
  .contact-icon {
    width: 20px;
    height: 20px;
    flex: none;
  }
  .postal-address {
    position: absolute;
    right: 38px;
    top: 374px;
    font-style: normal;
    font-size: 21px;
    line-height: 28px;
  }
  .card-brand {
    flex: 1;
    background: var(--panel-light);
    display: flex;
    align-items: center;
    justify-content: center;
  }
  .brand-name {
    font-family: "Exo 2", sans-serif;
    font-weight: 600;
    font-size: 60px;
    letter-spacing: 2px;
    color: var(--text-dark);
    margin-left: 10px;
  }
</style>
</head>
<body>
<main class="canvas">
  <article class="business-card">
    <section class="card-info">
      <h1 class="person-name">Marcus Ellery</h1>
      <p class="person-role">Managing Director</p>
      <svg class="name-chevron" viewBox="0 0 24 46" aria-hidden="true">
        <polygon points="24,0 24,8 9,23 24,38 24,46 1,23" fill="var(--accent)"/>
      </svg>

      <ul class="contact-list">
        <li>044-987 654 321
          <svg class="contact-icon" viewBox="0 0 20 20" aria-hidden="true">
            <path d="M3 7c0-2 3-3.5 7-3.5S17 5 17 7v1.5h-3.5V7h-7v1.5H3z M5.5 9.5h9l2 6h-13z" fill="var(--accent)"/>
            <circle cx="10" cy="13" r="1.8" fill="#000"/>
          </svg>
        </li>
        <li>044-987 654 321
          <svg class="contact-icon" viewBox="0 0 20 20" aria-hidden="true">
            <rect x="5.5" y="2" width="9" height="16" rx="1.5" fill="none" stroke="var(--accent)" stroke-width="1.8"/>
            <circle cx="10" cy="15.3" r="1" fill="var(--accent)"/>
          </svg>
        </li>
        <li>info@vendalo.com
          <svg class="contact-icon" viewBox="0 0 20 20" aria-hidden="true">
            <rect x="3" y="5" width="14" height="10" fill="var(--accent)"/>
            <polyline points="3,5 10,11 17,5" fill="none" stroke="#000" stroke-width="1.3"/>
          </svg>
        </li>
        <li>www.vendalo.com
          <svg class="contact-icon" viewBox="0 0 20 20" aria-hidden="true">
            <circle cx="10" cy="10" r="7" fill="var(--accent)"/>
            <path d="M6 7.5c1.5-.5 2.5.5 3 2s-.5 2.5 0 4M12 5c0 1.5 1.5 2 2.5 2.5M11.5 13.5c1-1 2.5-1 3.5-2" fill="none" stroke="#000" stroke-width="1.1"/>
          </svg>
        </li>
      </ul>

      <address class="postal-address">
        12345, Address Goes Here<br>
        Country Name, 123456
      </address>
    </section>

    <section class="card-brand">
      <span class="brand-name">Vendalo</span>
    </section>
  </article>
</main>
</body>
</html>
```